Business Card Design

We are a commercial real estate brokerage in San Francisco, leasing office buildings downtown.
I would like a clean, elegant look. Simple but powerful .

Industry/Entity Type

Business

Contact Information for Business Card

Derek Holloway
lic# 07258143
415.555.0172
derek@velt-commercial.example
velt-commercial.example

```html
<!DOCTYPE html>
<html lang="en">
<head>
<meta charset="utf-8">
<title>Velt Commercial – Business Card</title>
<link rel="stylesheet" href="https://fonts.googleapis.com/css2?family=Jost:wght@500&family=Open+Sans:wght@400;600&display=swap">
<style>
  :root {
    --page-bg: #e6e6e4;
    --card-dark: #0d0e10;
    --card-light: #f1f1f0;
    --panel-grey: #55595c;
    --accent-blue: #6b7fa3;
    --accent-blue-dark: #4f6389;
    --text-dark: #3b3d40;
    --text-white: #ffffff;
    --text-soft: #e2e4e6;
    --divider-dark: #4a4d52;
    --divider-light: #8a8d90;
  }
  * { box-sizing: border-box; margin: 0; padding: 0; }
  html, body {
    width: 1200px; height: 768px; overflow: hidden;
    background: var(--page-bg);
  }
  .canvas {
    width: 1200px; height: 768px;
    display: flex; align-items: center; justify-content: center; gap: 40px;
  }
  .card {
    position: relative;
    width: 540px; height: 309px;
    overflow: hidden;
    box-shadow: 0 6px 18px rgba(0,0,0,0.18);
  }
  .card--front { background: var(--card-dark); }
  .card--back  { background: var(--card-light); }

  .brand {
    position: absolute;
    display: flex; align-items: center; gap: 14px;
  }
  .brand__mark {
    width: 38px; height: 38px;
    background: var(--accent-blue);
  }
  .brand__rule { width: 1px; height: 66px; }
  .brand__name {
    font-family: "Jost", sans-serif;
    font-weight: 500;
    color: var(--accent-blue);
    line-height: 0.95;
    text-transform: uppercase;
  }
  .brand__name span { display: block; }
  .brand__name .brand__line-1 { font-size: 52px; letter-spacing: 1px; }
  .brand__name .brand__line-2 { font-size: 25px; letter-spacing: 1px; }

  .card--front .brand { left: 50%; top: 50%; transform: translate(-50%, -50%); }
  .card--front .brand__rule { background: var(--divider-dark); }

  .card--back .brand { left: 30px; top: 46px; }
  .card--back .brand__rule { background: var(--divider-light); }
  .card--back .brand__name .brand__line-1 { font-size: 44px; }
  .card--back .brand__name .brand__line-2 { font-size: 21px; }

  .wave { position: absolute; inset: 0; }

  .holder {
    position: absolute; right: 26px; top: 66px;
    text-align: right; font-family: "Open Sans", sans-serif;
  }
  .holder__name { font-weight: 600; font-size: 19px; color: var(--text-white); letter-spacing: 0.3px; }
  .holder__title { font-size: 11px; color: var(--text-soft); margin-top: 2px; }

  .contact {
    position: absolute; left: 30px; top: 170px;
    list-style: none; font-family: "Open Sans", sans-serif;
    font-size: 12.5px; color: var(--text-dark);
  }
  .contact li { display: flex; align-items: center; gap: 10px; height: 20px; }
  .contact svg { width: 12px; height: 12px; fill: var(--text-dark); flex: none; }

  .licence {
    position: absolute; right: 30px; bottom: 26px;
    font-family: "Open Sans", sans-serif; font-size: 13px; color: var(--text-dark);
  }
</style>
</head>
<body>
<main class="canvas">

  <section class="card card--front" aria-label="Card front">
    <div class="brand">
      <div class="brand__mark"></div>
      <div class="brand__rule"></div>
      <div class="brand__name"><span class="brand__line-1">Velt</span><span class="brand__line-2">Commercial</span></div>
    </div>
  </section>

  <section class="card card--back" aria-label="Card back">
    <svg class="wave" viewBox="0 0 540 309" preserveAspectRatio="none" aria-hidden="true">
      <path d="M190,0 C300,14 390,110 540,208 L540,0 Z" fill="var(--panel-grey)"/>
      <path d="M150,6 C280,10 380,100 540,212" fill="none" stroke="var(--accent-blue)" stroke-width="5"/>
      <path d="M170,16 C300,30 400,130 540,220" fill="none" stroke="var(--accent-blue-dark)" stroke-width="2"/>
    </svg>

    <div class="brand">
      <div class="brand__mark"></div>
      <div class="brand__rule"></div>
      <div class="brand__name"><span class="brand__line-1">Velt</span><span class="brand__line-2">Commercial</span></div>
    </div>

    <div class="holder">
      <p class="holder__name">Derek Holloway</p>
      <p class="holder__title">Managing Director</p>
    </div>

    <ul class="contact">
      <li>
        <svg viewBox="0 0 12 12"><path d="M2.5 1 L4.5 1 L5.2 3.6 L4 4.6 C4.6 6 6 7.4 7.4 8 L8.4 6.8 L11 7.5 L11 9.5 C11 10.3 10.3 11 9.5 11 C5 11 1 7 1 2.5 C1 1.7 1.7 1 2.5 1 Z"/></svg>
        <span>415.555.0172</span>
      </li>
      <li>
        <svg viewBox="0 0 12 12"><path d="M1 2.5 H11 V9.5 H1 Z M1.6 3 L6 6.6 L10.4 3" stroke="var(--card-light)" stroke-width="0.9"/></svg>
        <span>derek@velt-commercial.example</span>
      </li>
      <li>
        <svg viewBox="0 0 12 12"><circle cx="6" cy="6" r="5"/><path d="M1 6 H11 M6 1 C3.5 3.5 3.5 8.5 6 11 M6 1 C8.5 3.5 8.5 8.5 6 11" stroke="var(--card-light)" stroke-width="0.8" fill="none"/></svg>
        <span>www.velt-commercial.example</span>
      </li>
    </ul>

    <p class="licence">LIC# 07258143</p>
  </section>

</main>
</body>
</html>
```